Corvane Grid Works Ltd. -Website Design

We need a site design for a new company based in Toronto, Ontario called 'Corvane Grid Works Ltd.'

We provide Engineering services, Subsurface Utility Engineering services and Geospatial Data Management.

Our clients are typically Utilities (electric, gas, water/waste water, telcom) or contractors/consultants working on their behalf.

Our business model is new and we are the first to offer all three services to our clients; this allows us to provide value-added services from all three of our main offerings.

Target Market(s)

Field Supervisors, Managers, Directors, VP's at Utility companies

Industry/Entity Type

Business

Requirements
Must have
• -The landing page must clearly identify the 3 main business offerings allowing the user to easily navigate to each....Utility Engineering, GIS Data Management & Sub-surface Utility Engineering (SUE).

-Interactive contact page with integrated email

-based on existing logo design...
Nice to have
• -Ability to easily add/post news releases, updates, jobs, etc...

-Ability to integrate instructional YouTube video(s)

Should not have
• -Cannot be too cluttered....

```html
<!DOCTYPE html>
<html lang="en">
<head>
<meta charset="utf-8">
<title>Corvane Grid Works Ltd.</title>
<link rel="stylesheet" href="https://fonts.googleapis.com/css2?family=Ubuntu:wght@400;500;700&display=swap">
<style>
  :root {
    --header-dark: #1b1b1b;
    --nav-red: #c2432d;
    --nav-red-dark: #a8331f;
    --nav-active: #d98b0c;
    --accent-yellow: #f6d53c;
    --heading-red: #c0392b;
    --accent-orange: #e39b16;
    --about-blue: #4a7fb2;
    --link-blue: #3c6b99;
    --body-text: #333333;
    --band-grey: #f1f1f1;
    --divider: #d8d8d8;
    --contact-bar: #2b2b2b;
    --footer-dark: #1e1e1e;
    --footer-text: #d6d6d6;
    --white: #ffffff;
  }
  * { margin: 0; padding: 0; box-sizing: border-box; }
  html, body { width: 1050px; height: 1200px; overflow: hidden; background: var(--white); }
  body { position: relative; font-family: "Ubuntu", "Helvetica Neue", Arial, sans-serif; color: var(--body-text); }
  ul { list-style: none; }

  .site-header { position: absolute; left: 0; top: 0; width: 1050px; height: 162px;
    background: radial-gradient(ellipse at 50% 0%, #2c2c2c 0%, var(--header-dark) 70%); }
  .brand { position: absolute; left: 50px; top: 26px; display: flex; align-items: center; gap: 12px; }
  .brand-mark { width: 48px; height: 48px; background: var(--accent-orange); border-radius: 6px; }
  .brand-name { font-size: 30px; font-weight: 700; letter-spacing: 2px; color: var(--white); }
  .search { position: absolute; left: 834px; top: 40px; width: 170px; height: 24px; background: var(--white);
    border: 1px solid #bbb; border-radius: 2px; font-size: 11px; color: #aaa; font-style: italic; padding: 5px 11px; }
  .search svg { position: absolute; right: 6px; top: 6px; }

  .main-nav { position: absolute; left: 45px; top: 110px; width: 963px; height: 51px;
    background: linear-gradient(#cc4b33, var(--nav-red-dark)); display: flex; align-items: center; }
  .main-nav a { display: block; height: 51px; line-height: 51px; color: var(--white); text-decoration: none;
    font-size: 14px; text-align: center; border-right: 1px solid #9b2d1b; }
  .main-nav a.active { background: linear-gradient(#e39a18, #c97b06); color: #2a1a00; }
  .nav-contact { margin-left: auto; padding-right: 22px; font-size: 14px; color: var(--accent-yellow); }
  .nav-contact span { margin: 0 10px; }

  .hero { position: absolute; left: 45px; top: 163px; width: 963px; height: 280px;
    background: linear-gradient(100deg, #5f8fc0 0%, #8fb6dc 45%, #7aa6d3 75%, #3f6e9f 100%);
    border: 1px solid #2e4f70; box-shadow: 0 10px 10px -6px rgba(0,0,0,.45); }
  .hero-title { position: absolute; left: 245px; top: 63px; font-size: 17px; color: var(--white); letter-spacing: .3px; }
  .hero-btn { position: absolute; left: 247px; top: 101px; width: 87px; height: 32px; border-radius: 8px;
    background: linear-gradient(#ffffff, #dfe5ea); color: var(--link-blue); font-size: 12px; font-weight: 500;
    text-align: center; line-height: 32px; box-shadow: 0 2px 3px rgba(0,0,0,.3); }
  .hero-pager { position: absolute; left: 405px; bottom: -1px; width: 150px; height: 29px; }

  .services { position: absolute; left: 0; top: 469px; width: 1050px; height: 328px;
    background: linear-gradient(#f5f5f5, #ffffff 60%, #f7f7f7); }
  .service { position: absolute; top: 0; }
  .service h2 { font-size: 17px; font-weight: 500; color: var(--heading-red); line-height: 22px; padding: 17px 0 0 8px; height: 66px;
    background: linear-gradient(90deg, #eeeeee, #f6f6f6); }
  .service h2 em { font-style: normal; color: var(--accent-orange); }
  .service ul { margin-top: 10px; padding-left: 12px; }
  .service li { position: relative; padding-left: 15px; font-size: 12.5px; line-height: 16px; margin-bottom: 10px; }
  .service li::before { content: ""; position: absolute; left: 0; top: 4px; border-left: 5px solid #444;
    border-top: 4px solid transparent; border-bottom: 4px solid transparent; }
  .service li .sub { display: block; padding-left: 5px; }
  .service-1 { left: 45px; width: 277px; }
  .service-2 { left: 355px; width: 385px; }
  .service-2 ul li { margin-bottom: 8px; }
  .service-3 { left: 763px; width: 247px; }
  .service-3 ul li { margin-bottom: 8px; }
  .service-divider { position: absolute; top: 12px; width: 1px; height: 300px; background: var(--divider); }

  .about { position: absolute; left: 60px; top: 821px; width: 545px; }
  .about h2 { font-size: 17px; font-weight: 400; color: var(--about-blue); margin-bottom: 12px; }
  .about p { font-size: 12.5px; line-height: 22px; text-align: justify; }
  .about .more { display: block; text-align: right; margin-top: 8px; font-size: 12.5px; color: var(--link-blue); }

  .video { position: absolute; left: 638px; top: 819px; width: 359px; height: 202px; background: #050505;
    box-shadow: 0 8px 10px -4px rgba(0,0,0,.4); padding: 4px; }
  .video-frame { width: 351px; height: 176px;
    background: linear-gradient(135deg, #c9ced3 0%, #8f98a1 45%, #3a3f46 100%); position: relative; }
  .video-play { position: absolute; left: 160px; top: 73px; }
  .video-bar { position: absolute; left: 4px; bottom: 4px; width: 351px; height: 16px; }

  .contact-bar { position: absolute; left: 0; top: 1048px; width: 1050px; height: 56px; background: var(--contact-bar); }
  .contact-bar .label { position: absolute; left: 169px; top: 19px; font-size: 14px; color: #f1a81e; }
  .field { position: absolute; top: 15px; width: 170px; height: 24px; background: var(--white); border: 1px solid #999;
    font-size: 11px; font-style: italic; color: #aaa; padding: 5px 11px; }
  .submit { position: absolute; left: 818px; top: 15px; width: 62px; height: 25px; border-radius: 5px;
    background: linear-gradient(#f3ae28, #c77a06); color: #2a1800; font-size: 11px; font-weight: 700; text-align: center; line-height: 25px; }

  .site-footer { position: absolute; left: 0; top: 1104px; width: 1050px; height: 96px; background: var(--footer-dark); }
  .footer-brand { position: absolute; left: 55px; top: 18px; display: flex; align-items: center; gap: 8px; }
  .footer-brand .brand-mark { width: 32px; height: 32px; background: #555; border-radius: 4px; }
  .footer-brand .brand-name { font-size: 20px; color: #6a6a6a; letter-spacing: 2px; }
  .copyright { position: absolute; left: 59px; top: 59px; font-size: 11.5px; color: var(--footer-text); }
  .footer-links { position: absolute; right: 42px; top: 19px; font-size: 11.5px; color: var(--footer-text); }
  .footer-links span { margin: 0 6px; }
  .social { position: absolute; left: 886px; top: 51px; display: flex; gap: 7px; }
  .social i { width: 25px; height: 25px; border-radius: 50%; background: var(--white); display: block; }
</style>
</head>
<body>

<header class="site-header">
  <div class="brand"><span class="brand-mark"></span><span class="brand-name">CORVANE</span></div>
  <div class="search">Search
    <svg width="11" height="11" viewBox="0 0 11 11"><circle cx="4.5" cy="4.5" r="3.3" fill="none" stroke="#bbb" stroke-width="1.3"/><line x1="7" y1="7" x2="10" y2="10" stroke="#bbb" stroke-width="1.5"/></svg>
  </div>
  <nav class="main-nav">
    <a class="active" style="width:95px">HOME</a>
    <a style="width:106px">ABOUT US</a>
    <a style="width:128px">OUR SERVICES</a>
    <a style="width:77px">FAQV</a>
    <a style="width:117px;border-right:none">CONTACT US</a>
    <div class="nav-contact">CALL US : 289.555.0142<span>|</span>EMAIL : info@corvanegrid.ca</div>
  </nav>
</header>

<section class="hero" role="img" aria-label="Banner photo: a businessman touching a glowing network of contact icons beside a computer monitor">
  <div class="hero-title">NEMO ENIM IPSAM VOLUPTATEM QUIA VOLUPTAS</div>
  <div class="hero-btn">VIEW MORE</div>
  <svg class="hero-pager" viewBox="0 0 150 29">
    <path d="M0 29 Q8 29 12 14 Q15 2 28 2 H122 Q135 2 138 14 Q142 29 150 29 Z" fill="#2a2a2a"/>
    <circle cx="50" cy="15" r="4.5" fill="#fff"/>
    <circle cx="71" cy="15" r="4.5" fill="#555"/>
    <circle cx="92" cy="15" r="4.5" fill="#555"/>
    <circle cx="113" cy="15" r="4.5" fill="#555"/>
  </svg>
</section>

<section class="services">
  <div class="service service-1">
    <h2>1. UTILITY ENGINEERING</h2>
    <ul>
      <li>Project Management</li>
      <li>Outside Plant Network Design</li>
      <li>Utility Design and Permitting</li>
      <li>Project Management</li>
      <li>Surveys and Mapping (GPS)</li>
      <li>Pole line design and attachment permitting<span class="sub">(Pole Load Calculations)</span></li>
      <li>Specialty Permits for the Utility Industry<span class="sub">(Railway, MOT, Conservation Authority)</span></li>
      <li>Manhole and Duct Bank Design.</li>
    </ul>
  </div>
  <div class="service-divider" style="left:338px"></div>
  <div class="service service-2">
    <h2>2. GEOGRAPHIC INFORMATION<br>&nbsp;&nbsp;&nbsp;&nbsp;SYSTEMS <em>(GIS)</em></h2>
    <ul>
      <li>GIS Project Management</li>
      <li>Records Conversion for GIS Systems</li>
      <li>Landbase Data Management</li>
      <li>Data Translation and Transformation Between File Formats</li>
      <li>Hydro Asset Management using Geomatrix</li>
      <li>Spatial Data Analysis &amp; Manipulation</li>
      <li>Fibre Asset Management using Geomatrix &amp; LineTrace Software</li>
      <li>Custom Cartographic Mapping</li>
      <li>Engineering and Base Mapping using Geomatrix, DraftCore, MapLedger</li>
      <li>Geomatrix Customization &amp; Application Development</li>
    </ul>
  </div>
  <div class="service-divider" style="left:749px"></div>
  <div class="service service-3">
    <h2>3. SUBSURFACE UTILITY<br>&nbsp;&nbsp;&nbsp;&nbsp;ENGINEERING <em>(SUE)</em></h2>
    <ul>
      <li>Project Management;</li>
      <li>Consulting;</li>
      <li>Surveying;</li>
      <li>CAD Processing of Results.</li>
    </ul>
  </div>
</section>

<section class="about">
  <h2>ABOUT CORVANE</h2>
  <p>Sed ut perspiciatis unde omnis iste natus error sit voluptatem accusantium doloremque laudantium, totam rem aperiam, eaque ipsa quae ab illo inventore veritatis et quasi architecto beatae vitae dicta sunt explicabo. Nemo enim ipsam voluptatem quia voluptas sit aspernatur aut odit aut fugit, sed quia consequuntur magni dolores eos qui ratione voluptatem sequi nesciunt. But I must explain to you how all this mistaken idea of denouncing pleasure and praising pain was born and I will give you a complete account of the system, and expound the actual.</p>
  <span class="more">VIEW MORE</span>
</section>

<div class="video">
  <div class="video-frame" role="img" aria-label="Video still: a team of business professionals standing together">
    <svg class="video-play" width="36" height="36" viewBox="0 0 36 36"><circle cx="18" cy="18" r="17" fill="#e6e6e6" stroke="#666" stroke-width="1.5"/><path d="M14 11 L25 18 L14 25 Z" fill="#444"/></svg>
  </div>
  <svg class="video-bar" viewBox="0 0 351 16">
    <rect width="351" height="16" fill="#111"/>
    <rect x="11" y="4" width="2" height="7" fill="#fff"/><rect x="15" y="4" width="2" height="7" fill="#fff"/>
    <rect x="30" y="6" width="280" height="4" fill="#444"/>
    <rect x="30" y="6" width="6" height="4" fill="#ccc"/>
    <rect x="318" y="5" width="10" height="6" fill="#666"/>
    <rect x="336" y="5" width="8" height="6" fill="#888"/>
  </svg>
</div>

<section class="contact-bar">
  <div class="label">CONTACT US</div>
  <div class="field" style="left:274px">Name</div>
  <div class="field" style="left:455px">Email</div>
  <div class="field" style="left:636px">Phone</div>
  <div class="submit">SUBMIT</div>
</section>

<footer class="site-footer">
  <div class="footer-brand"><span class="brand-mark"></span><span class="brand-name">CORVANE</span></div>
  <div class="copyright">Copyright © 2012 www.corvanegrid &nbsp;&nbsp; All rights reserved</div>
  <div class="footer-links">Home<span>|</span>About Us<span>|</span>Our Services<span>|</span>FAQ<span>|</span>Contact Us<span>|</span>Sitemap</div>
  <div class="social"><i></i><i></i><i></i><i></i></div>
</footer>

</body>
</html>
```